Tolbek cards

I want a simple business card that pops.
Logo on one side.
On side two i want.
"Are you thinking about a new building on your property, or renovating an existing structure? Contact".....
Owners Name: Dale Whitacre
Owners Phone number: 610-555-0187
Address:4076 Copper Ridge RD, Ashcombe, PA 17390
Committed to Quality, Service, and Integrity

```html
<!DOCTYPE html>
<html lang="en">
<head>
<meta charset="utf-8">
<title>Tolbek Builders LLC – Business Cards</title>
<link href="https://fonts.googleapis.com/css2?family=Arimo:ital,wght@0,400;0,700;1,400&display=swap" rel="stylesheet">
<style>
  :root {
    --backdrop: #5b5b5b;
    --card-white: #ffffff;
    --brown-deep: #3b2a1c;
    --brown-text: #5a3c28;
    --brown-band: #4a3320;
    --bronze-light: #a48c74;
    --bronze-mid: #7c6149;
    --gray-text: #555555;
    --ink: #222222;
    --rule: #cfcfcf;
    --back-center: #9b836b;
    --back-edge: #553726;
    --name-light: #eadfcf;
  }
  html, body {
    margin: 0;
    padding: 0;
    width: 1200px;
    height: 1200px;
    overflow: hidden;
    background: var(--backdrop);
    font-family: "Arimo", Arial, sans-serif;
  }
  .card {
    position: absolute;
    left: 255px;
    width: 690px;
    height: 394px;
    box-sizing: border-box;
    overflow: hidden;
  }
  .card-front {
    top: 158px;
    background: var(--card-white);
  }
  .card-back {
    top: 651px;
    background: radial-gradient(ellipse 60% 75% at 50% 50%, var(--back-center) 0%, var(--bronze-mid) 50%, var(--back-edge) 100%);
  }
  .pitch {
    position: absolute;
    left: 49px;
    top: 34px;
    margin: 0;
    width: 236px;
    font-style: italic;
    font-size: 18.5px;
    line-height: 24px;
    color: var(--brown-text);
  }
  .brand {
    position: absolute;
    display: flex;
    align-items: center;
    gap: 10px;
  }
  .brand-front {
    left: 349px;
    top: 65px;
  }
  .brand-mark {
    display: block;
    width: 34px;
    height: 34px;
    background: var(--brown-deep);
  }
  .brand-name {
    font-weight: 700;
    font-size: 20px;
    letter-spacing: 0.3px;
    color: var(--brown-deep);
    white-space: nowrap;
  }
  .brand-back {
    left: 0;
    right: 0;
    top: 164px;
    justify-content: center;
    gap: 18px;
  }
  .brand-back .brand-mark {
    width: 62px;
    height: 62px;
    background: var(--name-light);
  }
  .brand-back .brand-name {
    font-size: 36px;
    letter-spacing: 1px;
    color: var(--name-light);
  }
  .owner {
    position: absolute;
    left: 49px;
    top: 254px;
    margin: 0;
    font-weight: 700;
    font-size: 25px;
    letter-spacing: 0.3px;
    color: var(--brown-deep);
  }
  .divider {
    position: absolute;
    left: 49px;
    top: 288px;
    width: 594px;
    height: 1px;
    background: var(--rule);
  }
  .phone {
    position: absolute;
    left: 49px;
    top: 297px;
    display: flex;
    align-items: center;
    gap: 7px;
    font-size: 16px;
    color: var(--gray-text);
  }
  .phone svg { width: 13px; height: 13px; }
  .address {
    position: absolute;
    right: 43px;
    top: 300px;
    font-size: 16px;
    color: var(--gray-text);
    white-space: nowrap;
  }
  .motto {
    position: absolute;
    left: 0;
    right: 0;
    top: 344px;
    text-align: center;
    font-size: 17px;
    color: var(--ink);
  }
  .band {
    position: absolute;
    bottom: 0;
    height: 16px;
  }
  .band-dark {
    left: 0;
    width: 419px;
    background: linear-gradient(90deg, var(--brown-band), #3f2b1a);
  }
  .band-light {
    left: 423px;
    right: 0;
    background: linear-gradient(90deg, var(--bronze-mid), var(--bronze-light) 60%, var(--bronze-mid));
  }
</style>
</head>
<body>
  <section class="card card-front">
    <p class="pitch">Are you thinking about a new building on your property, or renovating an existing structure?</p>
    <div class="brand brand-front">
      <span class="brand-mark"></span>
      <span class="brand-name">TOLBEK BUILDERS LLC</span>
    </div>
    <h1 class="owner">DALE WHITACRE</h1>
    <div class="divider"></div>
    <div class="phone">
      <svg viewBox="0 0 24 24" aria-hidden="true"><path fill="#3b2a1c" d="M6.6 10.8c1.4 2.8 3.8 5.1 6.6 6.6l2.2-2.2c.3-.3.7-.4 1-.2 1.1.4 2.3.6 3.6.6.6 0 1 .4 1 1V20c0 .6-.4 1-1 1C10.6 21 3 13.4 3 4c0-.6.4-1 1-1h3.5c.6 0 1 .4 1 1 0 1.3.2 2.5.6 3.6.1.3 0 .7-.2 1l-2.3 2.2z"/></svg>
      <span>610-555-0187</span>
    </div>
    <div class="address">4076 Copper Ridge RD, Ashcombe, PA 17390</div>
    <div class="motto">Committed to Quality, Service, and Integrity</div>
    <div class="band band-dark"></div>
    <div class="band band-light"></div>
  </section>

  <section class="card card-back">
    <div class="brand brand-back">
      <span class="brand-mark"></span>
      <span class="brand-name">TOLBEK BUILDERS LLC</span>
    </div>
  </section>
</body>
</html>
```